Web Developer Needs a Business Card Design

I need a personal business card design that represents me as a web developer for potential employers. I would like the background to be a dark color on the front for contrast with my logo and name. The back will have all my information along with a smaller version of the logo. I want something with a modern look and feel, not too conservative. This will be used for potential employers and freelance work.

Industry/Entity Type

Business

Contact Information for Business Card

Front should have my logo and name. The back should have all my personal information which would include: name: Tom Varulek, phone: 570-614-3098, email: tomvarulek@quillbox.net, website url: www.tomvarulek.net, logo, web developer.

Font styles to use
Sans Serif

Requirements
Must have
• Must include my logo. The color palette base color will be the logo color.

```html
<!DOCTYPE html>
<html lang="en">
<head>
<meta charset="utf-8">
<title>Tom Varulek – Business Card</title>
<link rel="stylesheet" href="https://fonts.googleapis.com/css2?family=Source+Sans+3:wght@300;400;600&display=swap">
<style>
  :root {
    --stage-top: #262626;
    --stage-bottom: #070707;
    --card-light: #f3f3f3;
    --brand-teal: #6cc6b4;
    --brand-teal-deep: #4fae9b;
    --ink: #1c1c1c;
    --white: #ffffff;
  }
  * { margin: 0; padding: 0; box-sizing: border-box; }
  html, body { width: 1200px; height: 900px; overflow: hidden; }
  body {
    position: relative;
    background: linear-gradient(180deg, var(--stage-top) 0%, var(--stage-bottom) 100%);
    font-family: "Source Sans 3", "Myriad Pro", Arial, sans-serif;
  }
  .card {
    position: absolute;
    top: 184px;
    width: 302px;
    height: 490px;
    border-radius: 12px;
    text-align: center;
  }
  .card--back { left: 299px; background: var(--card-light); }
  .card--front { left: 645px; width: 304px; background: var(--brand-teal); }

  .brand-mark {
    position: absolute;
    left: 50%;
    transform: translateX(-50%);
    display: flex;
    align-items: center;
    gap: 10px;
    font-weight: 600;
    white-space: nowrap;
  }
  .brand-mark__dot { border-radius: 50%; flex: none; }
  .card--back .brand-mark { top: 128px; color: var(--brand-teal); font-size: 30px; }
  .card--back .brand-mark__dot { width: 22px; height: 22px; background: var(--brand-teal); }
  .card--front .brand-mark { top: 226px; color: var(--brand-teal-deep); font-size: 38px; }
  .card--front .brand-mark__dot { width: 26px; height: 26px; background: var(--brand-teal-deep); }

  .card__name {
    position: absolute; left: 0; right: 0;
    font-weight: 600;
  }
  .card__role { position: absolute; left: 0; right: 0; }
  .card--back .card__name { top: 320px; font-size: 18px; color: var(--brand-teal); }
  .card--back .card__role { top: 342px; font-size: 14px; color: var(--ink); }
  .card--front .card__name { top: 369px; font-size: 34px; color: var(--white); }
  .card--front .card__role { top: 412px; font-size: 17px; color: var(--white); font-weight: 400; }

  .contact-list {
    position: absolute; left: 0; right: 0; top: 398px;
    list-style: none;
    font-size: 14px; color: var(--ink);
  }
  .contact-list li {
    display: flex; justify-content: center; align-items: center;
    gap: 5px; height: 20.5px;
  }
  .contact-list svg { width: 10px; height: 10px; fill: var(--brand-teal); flex: none; }
</style>
</head>
<body>
  <section class="card card--back" aria-label="Card back with contact details">
    <div class="brand-mark"><span class="brand-mark__dot"></span>Varulek</div>
    <h1 class="card__name">Tom Varulek</h1>
    <p class="card__role">Front-End Developer</p>
    <ul class="contact-list">
      <li>
        <svg viewBox="0 0 10 10" aria-hidden="true"><path d="M2 0.5 L3.6 2.6 L2.7 3.8 Q3.8 6.1 6.2 7.3 L7.4 6.4 L9.5 8 L8.3 9.5 Q4.5 9.3 1.5 6 Q0.3 4 0.5 2 Z"/></svg>
        570-614-3098
      </li>
      <li>
        <svg viewBox="0 0 10 10" aria-hidden="true"><path d="M0.5 2 H9.5 V8 H0.5 Z" /><path d="M0.8 2.3 L5 5.3 L9.2 2.3" fill="none" stroke="#f3f3f3" stroke-width="0.9"/></svg>
        tomvarulek@quillbox.net
      </li>
      <li>
        <svg viewBox="0 0 10 10" aria-hidden="true"><path d="M4 6 L6 4" stroke="#6cc6b4" stroke-width="1.2"/><rect x="5" y="0.8" width="4" height="3" rx="1.5" transform="rotate(-45 7 2.3)" fill="none" stroke="#6cc6b4" stroke-width="1.2"/><rect x="1" y="6.2" width="4" height="3" rx="1.5" transform="rotate(-45 3 7.7)" fill="none" stroke="#6cc6b4" stroke-width="1.2"/></svg>
        www.tomvarulek.net
      </li>
    </ul>
  </section>

  <section class="card card--front" aria-label="Card front">
    <div class="brand-mark"><span class="brand-mark__dot"></span>Varulek</div>
    <h2 class="card__name">Tom Varulek</h2>
    <p class="card__role">Front-End Developer</p>
  </section>
</body>
</html>
```